Business Card for a New Zealand IT Startup

I need a business card for VELTA Holdings. We are a young startup based in New Zealand working in internet marketing and web development. The design should have some element connected to New Zealand, such as wave, koru or silver fern, just don't use a kiwi bird.

```html
<!DOCTYPE html>
<html lang="en">
<head>
<meta charset="utf-8">
<title>VELTA Holdings – Business Card</title>
<link rel="stylesheet" href="https://fonts.googleapis.com/css2?family=Work+Sans:wght@400;500;700&display=swap">
<style>
  :root {
    --stage: #2b2d31;
    --card-white: #ffffff;
    --brand-blue: #0a6cb5;
    --brand-orange: #e85a24;
    --text-grey: #4a4a4a;
    --icon-blue: #1b7fd0;
  }
  * { margin: 0; padding: 0; box-sizing: border-box; }
  html, body {
    width: 1200px; height: 900px; overflow: hidden;
    background: var(--stage);
    font-family: "Work Sans", Arial, sans-serif;
  }
  .canvas {
    width: 1200px; height: 900px;
    display: flex; align-items: center; justify-content: center;
  }
  .card {
    position: relative;
    width: 1050px; height: 600px;
    background: var(--card-white);
    overflow: hidden;
    box-shadow: 0 12px 30px rgba(0,0,0,.45);
  }
  .card__band { position: absolute; inset: 0; }
  .card__holder {
    position: absolute; left: 46px; top: 40px;
    color: var(--card-white);
  }
  .card__name {
    font-size: 30px; font-weight: 500; letter-spacing: 1.5px;
    text-transform: uppercase;
  }
  .card__role { font-size: 18px; font-weight: 400; margin-top: 2px; }
  .card__brand {
    position: absolute; right: 60px; top: 330px;
    display: flex; align-items: center; gap: 14px;
  }
  .card__brand-name {
    font-size: 46px; font-weight: 700; color: var(--brand-blue);
    letter-spacing: 1px;
  }
  .card__brand-dot {
    width: 44px; height: 44px; border-radius: 50%;
    background: var(--brand-blue);
  }
  .card__contact {
    position: absolute; right: 60px; top: 418px;
    list-style: none; text-align: right;
    font-size: 21px; line-height: 31px; color: var(--text-grey);
  }
  .card__contact li { display: flex; justify-content: flex-end; align-items: center; gap: 10px; }
  .card__contact .icon { width: 16px; height: 16px; flex: none; }
  .card__contact .icon-gap { width: 16px; flex: none; }
  .card__web-domain { color: var(--brand-orange); }
</style>
</head>
<body>
<main class="canvas">
  <section class="card">
    <svg class="card__band" width="1050" height="600" viewBox="0 0 1050 600">
      <path d="M0 0 H1050 V190 L860 260 L0 300 Z" fill="var(--brand-blue)"/>
      <path role="img" aria-label="Silver fern frond illustration in orange, stretching across the card"
            d="M0 200 C200 130 500 150 700 185 C820 205 900 215 960 225 C900 250 820 265 700 285 C500 315 220 330 0 340 Z"
            fill="var(--brand-orange)" stroke="var(--card-white)" stroke-width="6"/>
    </svg>

    <div class="card__holder">
      <p class="card__name">Daniel Harper</p>
      <p class="card__role">Director</p>
    </div>

    <div class="card__brand">
      <span class="card__brand-name">VELTA Holdings</span>
      <span class="card__brand-dot"></span>
    </div>

    <ul class="card__contact">
      <li>48b Harbour Lane,<span class="icon-gap"></span></li>
      <li>Christchurch, NZ, 8013<span class="icon-gap"></span></li>
      <li>(555) 210-4871
        <svg class="icon" viewBox="0 0 16 16"><path d="M4 1 L7 4 L5 6 C6 8 8 10 10 11 L12 9 L15 12 L13 15 C7 14 2 9 1 3 Z" fill="var(--icon-blue)"/></svg>
      </li>
      <li>info@veltaholdings.com
        <svg class="icon" viewBox="0 0 16 16"><rect x="1" y="3" width="14" height="10" rx="1" fill="none" stroke="var(--icon-blue)" stroke-width="1.8"/><path d="M1 4 L8 9 L15 4" fill="none" stroke="var(--icon-blue)" stroke-width="1.8"/></svg>
      </li>
      <li><span>www.<span class="card__web-domain">veltaholdings</span>.com</span>
        <svg class="icon" viewBox="0 0 16 16"><circle cx="8" cy="8" r="6.5" fill="none" stroke="var(--icon-blue)" stroke-width="1.6"/><ellipse cx="8" cy="8" rx="3" ry="6.5" fill="none" stroke="var(--icon-blue)" stroke-width="1.4"/><path d="M1.5 8 H14.5" stroke="var(--icon-blue)" stroke-width="1.4"/></svg>
      </li>
    </ul>
  </section>
</main>
</body>
</html>
```